Need a landing page design updated

Need an existing landing page perfected, want it too look similar to one of Quorbel's landing pages in that it flows and is really aesthetically pleasing. The link to the landing page is below. I need this design updated asap. Please take the content directly from the page.

http://verdantmoxfl.com/residential-services/

Target Market(s)

High end residential landscape customers on the gulf coast of Florida (Clearwater area)

Industry/Entity Type

Landscape Gardening

Font styles to use
Sans Serif
Decorative

Requirements
Must have
• I want to keep the written content the same on on the landing page, but would like to work on making both aesthetically appealing to the consumer. This is for high end residential clients on the gulf coast of florida, so think palm trees and sunny beaches with beautiful houses and gorgeous landscapes....look through www.verdantmoxfl.com home page for an example of the houses we landscape.
Nice to have
• Would like it to flow as you scroll similar to Quorbel's landing pages.
• Look at how Quorbel's landing page flows, want similar here.....
• https://www.quorbel.com/zentaphone-v/
Should not have
• this landing page must be beautiful and must make a lot of sense as you scroll, am looking for a work of art....please do not submit generic templates or anything that can be easily done....I need real artistry.

```html
<!DOCTYPE html>
<html lang="en">
<head>
<meta charset="utf-8">
<title>Verdantmox — Residential</title>
<link href="https://fonts.googleapis.com/css2?family=Montserrat:wght@400;500;600;700;800&family=Lato:wght@400;700&display=swap" rel="stylesheet">
<style>
:root{
  --blue:#0ea5cf;
  --blue-dark:#0b8fb5;
  --ink:#2b2b2b;
  --body:#555;
  --light:#f5f5f5;
  --panel:#f1f1f1;
  --tick:#e2683c;
  --white:#fff;
}
*{box-sizing:border-box;margin:0;padding:0}
html,body{width:1200px;height:3846px;overflow:hidden}
body{position:relative;background:var(--white);font-family:"Lato",Arial,sans-serif;color:var(--body)}
.abs{position:absolute}

/* header */
.site-header{left:0;top:0;width:1200px;height:77px;background:var(--white)}
.brand{left:133px;top:18px;display:flex;align-items:center;gap:10px;font-family:"Montserrat",sans-serif;font-weight:600;font-size:27px;color:var(--blue-dark);letter-spacing:1px}
.brand-dot{width:14px;height:14px;border-radius:50%;background:var(--blue)}
.header-contact{right:133px;top:26px;text-align:right;font-size:12px;line-height:17px;color:#444}
.header-contact span{color:var(--blue)}
.main-nav{left:0;top:77px;width:1200px;height:31px;background:var(--blue);display:flex;gap:26px;padding-left:140px;align-items:center}
.main-nav a{color:var(--white);text-decoration:none;font-family:"Montserrat",sans-serif;font-size:11px;font-weight:600;text-transform:uppercase}

/* hero */
.hero{left:0;top:108px;width:1200px;height:466px;background:linear-gradient(180deg,#8fb9d6 0%,#c9d8e2 30%,#7e8f97 55%,#4f8a3a 70%,#3f7a2c 100%)}
.hero-title{left:0;top:290px;width:1200px;text-align:center;font-family:"Montserrat",sans-serif;font-weight:800;font-size:80px;color:var(--white);text-shadow:0 3px 10px rgba(0,0,0,.35)}

/* intro */
.intro-title{left:0;top:638px;width:1200px;text-align:center;font-family:"Montserrat",sans-serif;font-weight:500;font-size:60px;color:var(--ink)}
.intro-copy{left:170px;top:722px;width:860px;text-align:center;font-family:"Montserrat",sans-serif;font-size:17px;line-height:28px;color:var(--body)}
.intro-copy p+p{margin-top:20px}

/* blue band */
.blue-band{left:0;top:940px;width:1200px;height:1183px}
.band-lead{left:0;top:1085px;width:1200px;text-align:center;font-family:"Montserrat",sans-serif;font-size:16px;line-height:31px;color:var(--white)}
.compare-card{left:133px;top:1185px;width:934px;height:723px;background:var(--white)}
.compare-row{position:absolute;left:0;width:934px;overflow:hidden}
.row-generic{top:0;height:395px;background:var(--panel)}
.row-tailored{top:395px;height:328px;background:var(--panel)}
.photo-generic{position:absolute;inset:0;background:linear-gradient(180deg,#4f9fdc 0%,#a9d3ef 40%,#e9e2cf 58%,#58a43c 70%,#b07a5a 100%);clip-path:polygon(0 0,539px 0,405px 100%,0 100%)}
.photo-tailored{position:absolute;inset:0;background:linear-gradient(180deg,#5da8e0 0%,#bfe0f4 40%,#6aa0a0 55%,#4e9a2e 75%,#3f8a25 100%);clip-path:polygon(405px 0,100% 0,100% 100%,520px 100%)}
.service{position:absolute;width:330px}
.service h2{font-family:"Montserrat",sans-serif;font-weight:700;font-size:27px;line-height:34px;color:var(--ink);margin-bottom:16px}
.service ul{list-style:none}
.service li{position:relative;padding-left:18px;font-size:11.5px;line-height:17px;color:#666;margin-bottom:12px}
.service li svg{position:absolute;left:0;top:3px}
.service-generic{left:557px;top:95px}
.service-tailored{left:48px;top:95px}

/* benefits */
.benefits{left:0;top:2123px;width:1200px;height:467px;background:linear-gradient(180deg,#2c3a35 0%,#1f2a22 45%,#2f4a22 75%,#1a2616 100%)}
.benefits-title{left:0;top:2203px;width:1200px;text-align:center;font-family:"Montserrat",sans-serif;font-weight:700;font-size:30px;color:var(--white)}
.benefit-icon{width:112px;height:112px;border-radius:50%;background:var(--white);display:flex;align-items:center;justify-content:center}
.benefit-text{width:300px;text-align:center;font-size:13.5px;line-height:26px;color:var(--white)}

/* reasons */
.reasons{left:0;top:2590px;width:1200px;height:859px;background:var(--light)}
.reason-photo{width:200px;height:200px;border-radius:50%;border:3px dashed #d6d6d6;padding:6px;background:var(--light)}
.reason-photo div{width:100%;height:100%;border-radius:50%;background:linear-gradient(180deg,#3f8fdc 0%,#9cc8ec 40%,#c9b99a 58%,#4c9a2c 72%,#3a7e22 100%)}
.reason h3{font-family:"Montserrat",sans-serif;font-weight:400;font-size:19px;line-height:29px;color:var(--ink);margin-bottom:12px}
.reason p{font-size:11px;line-height:18px;color:#666;margin-bottom:10px}

/* cta */
.cta-copy{left:0;top:3520px;width:1200px;text-align:center;font-family:"Montserrat",sans-serif;font-size:18px;line-height:38px;color:var(--ink)}
.cta-form{left:133px;top:3630px;width:934px;display:flex;gap:12px}
.cta-form input{width:387px;height:38px;border:1px solid #ddd;border-radius:19px;padding:0 20px;font-family:"Lato",sans-serif;font-size:12px;color:#888;background:var(--white)}
.cta-form button{width:136px;height:38px;border:none;border-radius:19px;background:var(--blue);color:var(--white);font-family:"Montserrat",sans-serif;font-weight:700;font-size:13px;text-transform:uppercase}

/* footer */
.site-footer{left:0;top:3749px;width:1200px;height:97px;background:var(--blue);display:flex;align-items:center;justify-content:center;font-size:13px;color:var(--white)}
</style>
</head>
<body>

<header class="site-header abs">
  <div class="brand abs"><span class="brand-dot"></span>VERDANTMOX</div>
  <div class="header-contact abs"><span>Call Us Now On :</span> 727-555-0148<br>Client Portal | Get A Free Quote</div>
</header>
<nav class="main-nav abs">
  <a href="#">Home</a><a href="#">About Us</a><a href="#">Residential</a><a href="#">Commercial</a><a href="#">Blog</a><a href="#">Contact Us</a>
</nav>

<section class="hero abs" role="img" aria-label="Grey two-storey house with a stone path across a green lawn"></section>
<h1 class="hero-title abs">Residential</h1>

<h2 class="intro-title abs">Let’s Guess</h2>
<div class="intro-copy abs">
  <p>You don’t have an abundance of free time. And, you simply don’t want to spend the little time you have – mowing a lawn and pruning the plants.</p>
  <p>You would probably like to spend that time the way you should, instead. Enjoying the sunset in the privacy of your garden, watching a favorite TV show while lying on a hammock, or throwing an occasional BBQ party with your friends and loved ones.Right?</p>
</div>

<svg class="blue-band abs" viewBox="0 0 1200 1183" preserveAspectRatio="none" aria-hidden="true">
  <path d="M0 20 C150 -10 300 70 450 45 C600 20 700 -15 850 30 C980 70 1100 60 1200 25 L1200 1183 L0 1183 Z" fill="#0ea5cf"/>
</svg>
<p class="band-lead abs">Getting an outdoor area of your dreams is not that difficult, nor expensive.<br>You can make this happen by getting a help from a landscaping company that offers tailor-made services.</p>

<div class="compare-card abs">
  <div class="compare-row row-generic">
    <div class="photo-generic" role="img" aria-label="White villa with palm trees and a brick driveway"></div>
    <div class="service service-generic">
      <h2>Generic Landscaping Services</h2>
      <ul>
        <li><svg width="10" height="9" viewBox="0 0 10 9"><path d="M1 5l3 3 5-7" stroke="#e2683c" stroke-width="2" fill="none"/></svg>You pay for the bundle of services, regardless of whether you actually need them</li>
        <li><svg width="10" height="9" viewBox="0 0 10 9"><path d="M1 5l3 3 5-7" stroke="#e2683c" stroke-width="2" fill="none"/></svg>You get a generic service, not adjusted to the specific needs of your outdoor area</li>
        <li><svg width="10" height="9" viewBox="0 0 10 9"><path d="M1 5l3 3 5-7" stroke="#e2683c" stroke-width="2" fill="none"/></svg>The field team thinks of your property as just another task they have to complete</li>
      </ul>
    </div>
  </div>
  <div class="compare-row row-tailored">
    <div class="photo-tailored" role="img" aria-label="Palm trees over a lawn by the sea"></div>
    <div class="service service-tailored">
      <h2>Tailor-made Landscaping Services</h2>
      <ul>
        <li><svg width="10" height="9" viewBox="0 0 10 9"><path d="M1 5l3 3 5-7" stroke="#e2683c" stroke-width="2" fill="none"/></svg>You pay only for the services your yard really needs</li>
        <li><svg width="10" height="9" viewBox="0 0 10 9"><path d="M1 5l3 3 5-7" stroke="#e2683c" stroke-width="2" fill="none"/></svg>You get your garden's specific issues solved, and specific requirements met</li>
        <li><svg width="10" height="9" viewBox="0 0 10 9"><path d="M1 5l3 3 5-7" stroke="#e2683c" stroke-width="2" fill="none"/></svg>The field team members take their time working on your property</li>
        <li><svg width="10" height="9" viewBox="0 0 10 9"><path d="M1 5l3 3 5-7" stroke="#e2683c" stroke-width="2" fill="none"/></svg>They get to learn all about your vision – and make it a reality</li>
      </ul>
    </div>
  </div>
</div>

<section class="benefits abs" role="img" aria-label="Dark evening view of a house and a trimmed front lawn"></section>
<h2 class="benefits-title abs">More benefits of having a well-maintained yard:</h2>
<svg class="abs" style="left:325px;top:2320px" width="560" height="40" aria-hidden="true">
  <path d="M0 20 C80 40 200 40 272 18 M340 18 C420 0 500 0 560 20" stroke="#fff" stroke-width="1.5" stroke-dasharray="5 5" fill="none"/>
</svg>
<div class="benefit-icon abs" style="left:213px;top:2282px">
  <svg width="56" height="56" viewBox="0 0 56 56"><circle cx="22" cy="28" r="16" fill="none" stroke="#333" stroke-width="3"/><text x="22" y="35" text-anchor="middle" font-family="Montserrat,sans-serif" font-weight="700" font-size="20" fill="#333">$</text><rect x="38" y="14" width="14" height="5" fill="#333"/><rect x="38" y="23" width="14" height="5" fill="#333"/><rect x="38" y="32" width="14" height="5" fill="#333"/><rect x="38" y="41" width="14" height="5" fill="#333"/></svg>
</div>
<div class="benefit-icon abs" style="left:541px;top:2282px">
  <svg width="56" height="56" viewBox="0 0 56 56"><path d="M6 28 L28 8 L50 28" fill="none" stroke="#333" stroke-width="4"/><path d="M13 26 V48 H43 V26" fill="none" stroke="#333" stroke-width="4"/><rect x="23" y="33" width="10" height="15" fill="#333"/></svg>
</div>
<div class="benefit-icon abs" style="left:882px;top:2282px">
  <svg width="56" height="56" viewBox="0 0 56 56"><path d="M8 8 L22 30" stroke="#333" stroke-width="3"/><rect x="18" y="28" width="30" height="12" rx="3" fill="#333"/><circle cx="22" cy="44" r="6" fill="#333"/><circle cx="44" cy="44" r="6" fill="#333"/></svg>
</div>
<p class="benefit-text abs" style="left:119px;top:2418px">In some cases, a great-looking lawn can increase your property’s value up to 20%.</p>
<p class="benefit-text abs" style="left:447px;top:2418px">Your lawn and plants reduce the energy consumption – countering the warming effects of paved surfaces.</p>
<p class="benefit-text abs" style="left:788px;top:2418px">They act as good dust filters, increasing air quality, and removing carbon dioxide from the atmosphere.</p>

<section class="reasons abs"></section>
<div class="reason abs" style="left:133px;top:2692px;width:620px">
  <h3>Why should you care that Verdantmox employs the leading industry experts and uses modern, eco-friendly technical solutions?</h3>
  <p>That is why we’re able to transform your lawn into a green carpet and get your plants in a perfect health. All while keeping your vision and your budget on our minds.</p>
  <p>That is why our services actually enable you to reduce the operating expenses.</p>
</div>
<div class="reason-photo abs" style="left:849px;top:2669px"><div role="img" aria-label="House with palm trees and a green lawn"></div></div>

<div class="reason-photo abs" style="left:149px;top:2938px"><div role="img" aria-label="Family home with a landscaped front garden"></div></div>
<div class="reason abs" style="left:492px;top:2965px;width:580px">
  <h3>Do you worry our services are going to disturb you while trying to unwind in the privacy of your own garden?</h3>
  <p>Our Client Service Operators Build A Schedule Around Your Needs – Designed Not To Disturb You At All.</p>
</div>

<div class="reason abs" style="left:133px;top:3196px;width:640px">
  <h3>At Verdantmox, we do more than just keeping your landscape in a pristine state.</h3>
  <p>We are delighted with your landscaping, both with the design and implementation.It’s not very often these days that work exceeds expectations Verdantmox are efficient, on-time, responsive, provide fair pricing, do outstanding work, have great people, and actually follow up on their work.</p>
</div>
<div class="reason-photo abs" style="left:849px;top:3156px"><div role="img" aria-label="Palm-lined house with a manicured lawn"></div></div>

<p class="cta-copy abs">So, what’s the next step to enriching your living area? And getting you a garden from your dreams.<br>It’s simple, just book a no-obligations consultation</p>
<form class="cta-form abs">
  <input type="text" placeholder="Name" aria-label="Name">
  <input type="email" placeholder="Email" aria-label="Email">
  <button type="button">Get Started</button>
</form>

<footer class="site-footer abs">Copyright 2017 Verdantmox All Rights Reserved</footer>

</body>
</html>
```